In need of a Wordpress website for a Water Sports Rental Company!

We are starting a new venture that provides a variety of rental equipment in the Cayman Islands. We are in need of a website where guests are able to book their rental gear during their stay in Cayman. We will also have an interactive map where guests can learn about off the beaten path activities to explore in here Cayman.

Our target market is middle/upper class, so we need a website that appeals to this group. We need our website to be clean, simple and easy to navigate. We need it to be highly visual and modern. We like the idea of the website having a tropical feel to it, we are very open to creative ideas that reflects this!

Must be designed in WordPress using the Velmora template I’ve provided.

You will find all instructions & the photos I want to use for this website on the following stashvo account:
- www.stashvo.com
- Username: hello@lumentrips.com
- Password: pelican7

All of the photos will need to be resized accordingly to be as small as possible without loosing resolution.

These are the tabs that will be used:
- Home Page
- Adventure Map
- Rental Gear
- Tours
- Photo Gallery
- Contact Us

Home Page
- You will find all the text and instructions for the home page in the word document named ‘Home Page’.

Adventure Map
- You will find all the text and instructions for the home page in the word document named ‘Adventure Map Content’
- There will also be a few 'guide' pages under this tab, which we will go in to detail with the winner.

Rentals
- You will find all the text and instructions for the Rentals page in the word document named ‘Rentals Content’

Tours
- This will just be a page saying ‘kayaking, snorkeling & Bioluminescence tours coming soon’.

Photo Gallery
- You will find the photos for this in our Stashvo.com Account

Contact Us
- Send us a Message – page will be similar to our other site http://lumentrips.com/contact/
- Phone: +1 (345) 555 0192
- Email: hello@tidalotterco.com

The big factors on who will have the winning design are:
- The background used
- The layout of the Home Page
- The animations at the top of the Rental Landing Page
- The overall clean, professional look to the website

If you have any questions, don't hesitate to ask.

We look forward to working with you all!!

Good luck!!

Target Market(s)

Middle/Upper Class on vacation with their family

Industry/Entity Type

It Company

Coding

Coded - Design and coding required

Number of Pages Required

5+ page

Colors
fffbf0
cadf82
fbf289
f6faec
fdf9cf
eaf2ce
fff3d1
fee18a
abd037

Requirements
Must have
• - Must be designed in Wordpress using the Velmora template I have provided or another suitable web template.
• - Must be Responsive Web Design so that the website adjusts to various screen sizes.

```html
<!DOCTYPE html>
<html lang="en">
<head>
<meta charset="utf-8">
<title>Tidal Otter – Cayman's Premier Adventure and Rental Company</title>
<link href="https://fonts.googleapis.com/css2?family=Open+Sans:wght@400;600;700&display=swap" rel="stylesheet">
<style>
:root{
  --green:#abd037;
  --green-soft:#cadf82;
  --yellow:#fee18a;
  --cream:#fffbf0;
  --band:#f2f2f2;
  --page-bg:#e4e7e7;
  --ink:#333333;
  --body:#666666;
  --rule:#d0d0d0;
  --white:#ffffff;
  --sea-deep:#1f7fae;
  --sea:#3db4d0;
  --sea-light:#8fe0e4;
}
*{margin:0;padding:0;box-sizing:border-box}
html,body{width:1200px;height:4423px;overflow:hidden}
body{font-family:"Open Sans",Arial,sans-serif;color:var(--ink);
  background:
    radial-gradient(ellipse 260px 140px at 8% 6%,rgba(255,255,255,.8),transparent 70%),
    radial-gradient(ellipse 300px 180px at 94% 14%,rgba(255,255,255,.75),transparent 70%),
    radial-gradient(ellipse 240px 200px at 4% 30%,rgba(200,206,206,.7),transparent 70%),
    radial-gradient(ellipse 280px 160px at 96% 38%,rgba(255,255,255,.8),transparent 70%),
    radial-gradient(ellipse 260px 220px at 6% 52%,rgba(255,255,255,.75),transparent 70%),
    radial-gradient(ellipse 240px 180px at 95% 60%,rgba(198,204,204,.7),transparent 70%),
    radial-gradient(ellipse 280px 200px at 5% 74%,rgba(205,210,210,.7),transparent 70%),
    radial-gradient(ellipse 300px 200px at 95% 84%,rgba(255,255,255,.8),transparent 70%),
    radial-gradient(ellipse 260px 180px at 6% 94%,rgba(255,255,255,.75),transparent 70%),
    repeating-linear-gradient(125deg,rgba(255,255,255,.22) 0 18px,rgba(190,196,196,.18) 18px 40px,rgba(255,255,255,.12) 40px 66px),
    var(--page-bg)}
.site{position:absolute;left:88px;top:0;width:1024px;height:4423px;background:var(--white)}
.abs{position:absolute}

/* header */
.brand{left:0;top:62px;width:1024px;text-align:center}
.brand-mark{display:inline-flex;align-items:center;gap:14px;font-weight:700;font-size:34px;color:var(--ink)}
.brand-dot{width:42px;height:42px;border-radius:50%;background:var(--green)}
.tagline{left:0;top:170px;width:1024px;text-align:center;font-size:15px;color:#555}

.nav{left:0;top:212px;width:1024px;height:59px;background:var(--green);display:flex;align-items:center}
.nav a{color:var(--white);font-size:14px;text-decoration:none;text-transform:uppercase;height:59px;line-height:59px;text-align:center}
.nav a.active{background:var(--yellow);color:#6b6b2c;width:102px}
.nav .item{flex:1}

.hero{left:0;top:271px;width:1024px;height:531px;overflow:hidden;
  background:
    radial-gradient(ellipse 180px 260px at 50% 45%,rgba(255,214,90,.55),transparent 70%),
    radial-gradient(ellipse 260px 120px at 72% 65%,rgba(250,240,200,.35),transparent 70%),
    radial-gradient(ellipse 220px 120px at 20% 70%,rgba(240,230,190,.35),transparent 70%),
    radial-gradient(ellipse 600px 200px at 50% 0%,rgba(220,250,255,.6),transparent 70%),
    linear-gradient(180deg,#2b8cc0 0%,#2fa6cf 35%,#4cc2d6 70%,#9ad9d5 100%);
  box-shadow:0 6px 10px rgba(0,0,0,.15)}
.hero-title{left:0;top:300px;width:1024px;text-align:center;color:var(--white);font-weight:700;font-size:42px;letter-spacing:1px;text-shadow:0 2px 6px rgba(0,0,0,.45)}
.hero-play{left:483px;top:196px}
.hero-arrow{top:206px}

/* feature cards */
.feature{top:855px;width:310px;height:295px;background:var(--white);box-shadow:0 1px 5px rgba(0,0,0,.18)}
.feature .photo{height:183px}
.feature h3{margin-top:22px;font-size:15px;font-weight:400;text-align:center;text-transform:uppercase}
.feature p{margin:8px 30px 0;font-size:12px;line-height:1.5;color:var(--body);text-align:center}

/* welcome */
.welcome{left:0;top:1224px;width:1024px;height:251px;background:var(--band);text-align:center;padding:58px 58px 0}
.welcome h2{font-size:26px;font-weight:400;margin-bottom:20px}
.welcome p{font-size:13.5px;line-height:1.65;color:var(--body)}

/* story rows */
.row{left:0;width:1024px;height:313px}
.ring{position:absolute;top:0;width:236px;height:236px;border-radius:50%;border:3px solid var(--green-soft);padding:6px;background:var(--white)}
.ring .photo{width:100%;height:100%;border-radius:50%}
.row .copy{position:absolute}
.row h3{font-size:18px;font-weight:400;margin-bottom:10px;line-height:1.4}
.row p{font-size:13px;line-height:1.85;color:var(--body)}
.btn{display:inline-block;margin-top:14px;background:var(--green);color:var(--white);font-size:11px;font-weight:600;border-radius:15px;padding:7px 16px}
.divider{position:absolute;left:360px;width:580px;height:1px;background:var(--rule);top:281px}
.copy-right{left:360px;width:565px}
.copy-left{left:83px;width:585px}
.ring-left{left:89px}
.ring-right{left:697px}

/* top picks */
.picks{left:0;top:3761px;width:1024px;height:443px;background:var(--band)}
.picks h2{position:absolute;top:38px;width:1024px;text-align:center;font-size:26px;font-weight:400}
.pick{top:103px;width:233px;height:281px;background:var(--white);box-shadow:0 1px 4px rgba(0,0,0,.15);text-align:center}
.pick .photo{height:142px}
.pick h4{margin-top:16px;font-size:13px;font-weight:400;text-transform:uppercase}
.pick p{margin:6px 18px 0;font-size:11px;line-height:1.5;color:var(--body)}
.pill{display:inline-block;margin-top:10px;border:1px solid #999;border-radius:12px;padding:3px 18px;font-size:11px;color:#555}

/* footer */
.footer-links{left:0;top:4274px;width:1024px;text-align:center;font-size:12px;color:#444;word-spacing:6px}
.social{left:0;top:4310px;width:1024px;display:flex;justify-content:center;gap:8px}
.social span{width:24px;height:24px;border-radius:50%;border:1.5px solid #555}
.copyright{left:0;top:4346px;width:1024px;text-align:center;font-size:11px;color:#666}
</style>
</head>
<body>
<div class="site">
  <header>
    <div class="abs brand"><span class="brand-mark"><span class="brand-dot"></span>Tidal Otter</span></div>
    <div class="abs tagline">Cayman's Premier Adventure and Rental Company</div>
    <nav class="abs nav">
      <a class="active">Home</a>
      <a class="item">Adventure Map</a>
      <a class="item">Rental Gear</a>
      <a class="item">Tours</a>
      <a class="item">Photo Gallery</a>
      <a class="item">Contact Us</a>
    </nav>
  </header>

  <section class="abs hero" role="img" aria-label="Snorkeler underwater among tropical fish">
    <svg class="abs hero-arrow" style="left:18px" width="40" height="40"><circle cx="20" cy="20" r="19" fill="rgba(255,255,255,.35)"/><path d="M24 12 L16 20 L24 28" stroke="#fff" stroke-width="3" fill="none"/></svg>
    <svg class="abs hero-arrow" style="left:966px" width="40" height="40"><circle cx="20" cy="20" r="19" fill="rgba(255,255,255,.35)"/><path d="M16 12 L24 20 L16 28" stroke="#fff" stroke-width="3" fill="none"/></svg>
    <svg class="abs hero-play" width="58" height="58"><circle cx="29" cy="29" r="28" fill="rgba(0,0,0,.35)"/><path d="M23 17 L41 29 L23 41 Z" fill="#fff"/></svg>
    <div class="abs hero-title">TIDAL OTTER</div>
  </section>

  <article class="abs feature" style="left:33px">
    <div class="photo" role="img" aria-label="Two people paddling a blue kayak on clear water" style="background:radial-gradient(ellipse 120px 40px at 50% 62%,rgba(40,70,180,.75),transparent 75%),linear-gradient(#7fd6dc,#3aa9c2 60%,#2a8db0)"></div>
    <h3>Exploration</h3><p>Rent everything you need to get outside and explore the island on your own</p>
  </article>
  <article class="abs feature" style="left:357px">
    <div class="photo" role="img" aria-label="Person relaxing in an inflatable kayak in turquoise water" style="background:radial-gradient(ellipse 100px 36px at 55% 55%,rgba(60,60,170,.65),transparent 75%),linear-gradient(#8adfe0,#45b9cc 60%,#2f9cb6)"></div>
    <h3>Relaxation</h3><p>We will come straight to your resort or condo and set everything up for you</p>
  </article>
  <article class="abs feature" style="left:679px">
    <div class="photo" role="img" aria-label="Placeholder image for education" style="background:radial-gradient(ellipse 110px 40px at 50% 50%,rgba(210,60,60,.35),transparent 75%),linear-gradient(#f6f6f6,#e0e0e0)"></div>
    <h3>Education</h3><p>We love sharing our knowledge on Cayman's history and the island's</p>
  </article>

  <section class="abs welcome">
    <h2>WELCOME TO TIDAL OTTER</h2>
    <p>We love having the freedom to explore when travelling and we bet you do to! We are Grand Cayman's premier rental company, offering everything you need to make the most of your vacation. Our website serves as a great starting point to help you prepare for your vacation here in Cayman. We feature a huge selection of adventures on our interactive map with tons of useful information, pictures and directions. Our adventure map is the perfect guide to all our great spots to check out here in Cayman.</p>
  </section>

  <section class="abs row" style="top:1569px">
    <div class="ring ring-left"><div class="photo" role="img" aria-label="Aerial view of kayaks on clear shallow water" style="background:radial-gradient(circle at 40% 40%,rgba(60,80,190,.55) 0 14%,transparent 28%),radial-gradient(circle at 62% 62%,rgba(220,90,140,.45) 0 10%,transparent 22%),radial-gradient(circle,#79dcd6,#2c9fb2)"></div></div>
    <div class="copy copy-right" style="top:40px"><h3>Your one stop shop for all the rentals you need here in Cayman!</h3><p>We have a have a huge array of fun toys and equipment for you to enjoy. Whether it's for exploring or relaxing, we have all the equipment you need to make the most of your trip here in Cayman. Need something that we don't stock, just ask and we'll do everything we can to get you the gear you need!</p><span class="btn">Read More »</span></div>
    <div class="divider"></div>
  </section>

  <section class="abs row" style="top:1888px">
    <div class="copy copy-left" style="top:55px"><h3>Check out our interactive map of Cayman!</h3><p>You won't find any tourist traps on our map! We're all about getting off the beaten path and finding those unique spots and natural wonders to explore. Get our expert advice on which adventures are best for you and how to tackle them!</p><span class="btn">Read More »</span></div>
    <div class="ring ring-right"><div class="photo" role="img" aria-label="Illustrated map of the island" style="background:radial-gradient(ellipse 70px 40px at 55% 50%,rgba(240,200,90,.8),transparent 80%),radial-gradient(ellipse 40px 20px at 30% 35%,rgba(240,200,90,.7),transparent 80%),radial-gradient(circle,#bfe8f0,#5fb8d6)"></div></div>
    <div class="divider"></div>
  </section>

  <section class="abs row" style="top:2198px">
    <div class="ring ring-left"><div class="photo" role="img" aria-label="Two people in an inflatable kayak" style="background:radial-gradient(ellipse 100px 30px at 50% 64%,rgba(40,80,190,.7),transparent 80%),linear-gradient(#b9e4f4 0%,#7cc8e6 40%,#3a9fc8 100%)"></div></div>
    <div class="copy copy-right" style="top:48px"><h3>Enjoy Complete freedom to explore.</h3><p>Inflatable kayaks have revolutionized the way kayak exploration is done in a way never before. Our kayaks give you the freedom to explore Cayman's most secluded locations and snorkel those hard to reach reefs. Our kayaks are light, comfortable and easy to use.</p><span class="btn">Read More »</span></div>
    <div class="divider"></div>
  </section>

  <section class="abs row" style="top:2513px">
    <div class="copy copy-left" style="top:40px"><h3>There's no easier way to get around the island.</h3><p>What better way is there to explore the island other than to rent a bike and go? Our mountain bikes are perfect for those interested on heading out on a full day adventure. If you're looking for something more casual, renting a cruiser is perfect to get around the Seven Mile Beach area. Use our map to help guide you to all our suggested locations to</p><span class="btn">Read More »</span></div>
    <div class="ring ring-right"><div class="photo" role="img" aria-label="Beach cruiser bikes on the sand by the sea" style="background:radial-gradient(ellipse 70px 40px at 40% 60%,rgba(200,50,50,.55),transparent 80%),linear-gradient(#a9dcf0 0%,#7cc6e0 40%,#e6d8b8 62%,#d2bf98 100%)"></div></div>
    <div class="divider"></div>
  </section>

  <section class="abs row" style="top:2823px">
    <div class="ring ring-left"><div class="photo" role="img" aria-label="Placeholder image for concierge service" style="background:radial-gradient(ellipse 90px 34px at 50% 50%,rgba(210,60,60,.35),transparent 80%),radial-gradient(circle,#fafafa,#e2e2e2)"></div></div>
    <div class="copy copy-right" style="top:36px"><h3>We want to be your personal concierge and help you to plan out your trip!</h3><p>When we come to deliver your equipment, we teach you everything you need to know about the island including the best hidden spots, best restaurants &amp; bars to eat &amp; drink and anything else you might be curious about. Please don't hesitate to contact us for any and all of your vacation questions. We are happy to help!</p><span class="btn">Read More »</span></div>
    <div class="divider"></div>
  </section>

  <section class="abs row" style="top:3142px">
    <div class="copy copy-left" style="top:50px"><h3>Is it a boat? is it a whale?.... It's a Floatnest!</h3><p>Easily one of the coolest inventions we've ever come across, the Floatnest is a versatile toy the whole family can enjoy together. Spend the day cruising along Seven Mile Beach in style as you bar hop with your clan. Better still, bring a cooler on board and put the kids to work paddling as you relax in your hammock on the crystal clear waters!</p><span class="btn">Read More »</span></div>
    <div class="ring ring-right"><div class="photo" role="img" aria-label="Floating hammock craft on turquoise water" style="background:radial-gradient(ellipse 80px 50px at 50% 50%,rgba(40,70,110,.45),transparent 80%),radial-gradient(circle,#7fe0dc,#2f9bb5)"></div></div>
    <div class="divider"></div>
  </section>

  <section class="abs row" style="top:3457px">
    <div class="ring ring-left"><div class="photo" role="img" aria-label="Child wearing a full face snorkel mask underwater" style="background:radial-gradient(circle at 50% 45%,#f4b2d6 0 22%,#e08cc0 34%,transparent 55%),radial-gradient(circle,#6fd2e0,#2f9fc2)"></div></div>
    <div class="copy copy-right" style="top:42px"><h3>A new way to Snorkel!</h3><p>Our full face snorkel masks are easy to use, making them perfect for kids and beginners. You simply put the mask on and breath as you usually would. There's no need to get used to breathing from your mouth and you don't experience a sore jaw from having to hold the mouth piece in place. Just ask and we'll bring one along for you to try!</p><span class="btn">Read More »</span></div>
  </section>

  <section class="abs picks">
    <h2>OUR ADVENTURE TOP-PICKS</h2>
    <article class="abs pick" style="left:30px">
      <div class="photo" role="img" aria-label="Glowing blue bioluminescent bay at night" style="background:radial-gradient(ellipse 120px 40px at 50% 70%,rgba(40,170,255,.8),transparent 80%),linear-gradient(#050d1e,#0c2d55 60%,#134d88)"></div>
      <h4>Bio Bay</h4><p>We love having the freedom to explore when travelling and we bet you</p><span class="pill">View More</span>
    </article>
    <article class="abs pick" style="left:272px">
      <div class="photo" role="img" aria-label="Underwater shipwreck" style="background:radial-gradient(ellipse 90px 40px at 50% 55%,rgba(20,40,50,.6),transparent 80%),linear-gradient(#4aa6bd,#1f6a84 60%,#184f62)"></div>
      <h4>Kittiwake</h4><p>We love having the freedom to explore when travelling and we bet you</p><span class="pill">View More</span>
    </article>
    <article class="abs pick" style="left:513px">
      <div class="photo" role="img" aria-label="Aerial view of a small sandy cay" style="background:radial-gradient(ellipse 70px 40px at 50% 50%,#f2ead0,#d9cfa6 50%,transparent 80%),linear-gradient(#3f96ab,#2b7d92)"></div>
      <h4>Sand Cay Island</h4><p>We love having the freedom to explore when travelling and we bet you</p><span class="pill">View More</span>
    </article>
    <article class="abs pick" style="left:755px">
      <div class="photo" role="img" aria-label="Stingrays in shallow water" style="background:radial-gradient(ellipse 60px 30px at 40% 55%,rgba(70,80,80,.45),transparent 80%),linear-gradient(#93d3d6,#5eaab6 60%,#3e8f9f)"></div>
      <h4>Stingray City</h4><p>We love having the freedom to explore when travelling and we bet you</p><span class="pill">View More</span>
    </article>
  </section>

  <footer>
    <div class="abs footer-links">ABOUT | PRIVACY | TERMS | LEGAL | CONTACT</div>
    <div class="abs social"><span></span><span></span><span></span><span></span><span></span></div>
    <div class="abs copyright">Copyright © 2017. All Rights Reserved</div>
  </footer>
</div>
</body>
</html>
```